Graphics Design of Physics Book

Hi
Size : 8" x 11.25"
We are education book Publication Company and would like to have book cover for "Physics" it has 4 volumes. All 4 having the same color scheme and design except the volume no.
Blue is my personal favorite but u can use any color. Want to have a band at the bottom of the cover to place our Logo “VORNA Education” a PDF of the same is attached, or you can place logo anywhere according to ur design.
I need “Physics” as title of the book to be visible prominently.
And volume and volume no. should also be Visible and eye catching I prefer a Graphic to enhance the Volume No.
A background pattern can also be a option (it should be vector form so that color can be change later)
Please do not offer any cut and paste design I need very professional presentation.
Volume and Number can be in metallic 3D (CMYK) effect.
only Professional presentation will get feedback.
I have provided a sample artwork for reference do not follow it but can be a reference what I needed !

Target Market(s)

Students Class 9th to 12th

Industry/Entity Type

Education

Font styles to use
Serif

Colors
3176b5
0555a3
85abd2
cadf82
abd036
9bcb3c

Requirements
Must have
• Eye catching.
• “Physics” as title of the book to be visible prominently.
• volume and volume no. should also be Visible and eye catching
• I prefer a Graphic to enhance the Volume No.
• Icons for
• 1. Questions and answers
• 2. Theory Notes
• 3. Tips & Tricks
• 4. Previous Year's Reference Questions
• 5. Covers Complete Syllabus
Nice to have
• decent seamless background or metallic 3d effect (not to be print in special Ink) design should only be in CMYK.
Should not have
• Physics related Pictures or Icons (Specially E=mc2) or any scientist photograph or I Need pure graphic design

```html
<!DOCTYPE html>
<html lang="en">
<head>
<meta charset="utf-8">
<title>Physics Volume 1 – Book Cover</title>
<link href="https://fonts.googleapis.com/css2?family=Open+Sans:ital,wght@0,600;0,700;0,800;1,400;1,600;1,800&display=swap" rel="stylesheet">
<style>
  :root {
    --page-bg: #f2f3f5;
    --cover-white: #ffffff;
    --brand-blue: #1b9be0;
    --brand-blue-deep: #0a7fc4;
    --label-blue: #1e8fd2;
    --swoosh-grey: #a9abae;
    --icon-grey: #8d9093;
    --night-teal: #0b2b30;
    --night-teal-light: #134d52;
    --ink: #1d3a5c;
  }
  * { margin: 0; padding: 0; box-sizing: border-box; }
  html, body {
    width: 1200px;
    height: 976px;
    overflow: hidden;
    background: var(--page-bg);
    font-family: "Open Sans", Arial, sans-serif;
  }
  .spread {
    position: absolute;
    top: 80px;
    left: 14px;
    display: flex;
    gap: 12px;
  }
  .cover {
    width: 580px;
    height: 816px;
    background: var(--cover-white);
    box-shadow: 0 4px 18px rgba(0,0,0,0.15);
    position: relative;
    overflow: hidden;
  }
  .cover svg { display: block; }
  .cover-title {
    font-family: "Open Sans", Arial, sans-serif;
    font-style: italic;
    font-weight: 800;
    font-size: 84px;
    letter-spacing: 5px;
    fill: var(--cover-white);
  }
  .feature-label {
    font-family: "Open Sans", Arial, sans-serif;
    font-style: italic;
    font-weight: 600;
    font-size: 15px;
    fill: var(--label-blue);
  }
  .volume-mark {
    font-family: "Open Sans", Arial, sans-serif;
    font-weight: 800;
    font-size: 80px;
    letter-spacing: 2px;
  }
  .publisher {
    position: absolute;
    left: 30px;
    top: 452px;
    display: flex;
    align-items: center;
    gap: 8px;
  }
  .publisher-square {
    width: 14px;
    height: 14px;
    background: var(--brand-blue-deep);
  }
  .publisher-name {
    font-family: "Open Sans", Arial, sans-serif;
    font-weight: 700;
    font-size: 16px;
    color: var(--brand-blue-deep);
    letter-spacing: 0.5px;
  }
</style>
</head>
<body>
<main class="spread">

  <!-- Back cover -->
  <section class="cover cover--back" aria-label="Back cover">
    <svg width="580" height="816" viewBox="0 0 580 816" aria-hidden="true">
      <rect class="spine-strip" x="556" y="0" width="24" height="560" fill="var(--brand-blue)"/>
      <g role="img" aria-label="Dark teal field of glowing formulas and light points">
        <path d="M0,690 C160,650 330,700 460,600 C510,565 545,555 580,545 V816 H0 Z" fill="url(#nightFieldBack)"/>
      </g>
      <path d="M0,675 C160,635 330,685 460,585 C510,550 545,540 580,530" fill="none" stroke="var(--swoosh-grey)" stroke-width="8"/>
      <defs>
        <linearGradient id="nightFieldBack" x1="0" y1="1" x2="1" y2="0">
          <stop offset="0" stop-color="#0a2226"/>
          <stop offset="0.6" stop-color="#134d52"/>
          <stop offset="1" stop-color="#3a4a2a"/>
        </linearGradient>
      </defs>
    </svg>
    <div class="publisher">
      <span class="publisher-square"></span>
      <span class="publisher-name">VORNA Education</span>
    </div>
  </section>

  <!-- Front cover -->
  <section class="cover cover--front" aria-label="Front cover">
    <svg width="580" height="816" viewBox="0 0 580 816">
      <defs>
        <linearGradient id="blueBand" x1="0" y1="0" x2="0" y2="1">
          <stop offset="0" stop-color="#1592d8"/>
          <stop offset="1" stop-color="#28a8ea"/>
        </linearGradient>
        <linearGradient id="nightField" x1="0" y1="1" x2="1" y2="0">
          <stop offset="0" stop-color="#081f23"/>
          <stop offset="0.45" stop-color="#0f4348"/>
          <stop offset="0.75" stop-color="#1a5a5c"/>
          <stop offset="1" stop-color="#4b4a22"/>
        </linearGradient>
        <linearGradient id="metalSilver" x1="0" y1="0" x2="0" y2="1">
          <stop offset="0" stop-color="#ffffff"/>
          <stop offset="0.45" stop-color="#d9dcdf"/>
          <stop offset="0.55" stop-color="#8e9398"/>
          <stop offset="1" stop-color="#eef0f2"/>
        </linearGradient>
        <filter id="titleShadow" x="-10%" y="-20%" width="120%" height="150%">
          <feDropShadow dx="3" dy="4" stdDeviation="1.5" flood-color="#0b3a5c" flood-opacity="0.7"/>
        </filter>
        <filter id="metalDepth" x="-10%" y="-20%" width="120%" height="150%">
          <feDropShadow dx="4" dy="5" stdDeviation="2" flood-color="#000" flood-opacity="0.75"/>
        </filter>
      </defs>

      <!-- Title band -->
      <path class="title-band" d="M0,0 H580 V300 C470,248 380,205 260,214 C160,222 80,248 0,238 Z" fill="url(#blueBand)"/>
      <path class="title-swoosh" d="M0,256 C80,266 160,240 260,232 C380,223 470,266 580,318" fill="none" stroke="var(--swoosh-grey)" stroke-width="10"/>
      <text class="cover-title" x="300" y="150" text-anchor="middle" filter="url(#titleShadow)">PHYSICS</text>

      <!-- Feature icons -->
      <g class="feature feature--qa" transform="translate(105,270)">
        <ellipse cx="0" cy="22" rx="30" ry="22" fill="var(--brand-blue)"/>
        <path d="M-18,38 L-26,54 L-4,42 Z" fill="var(--brand-blue)"/>
        <text x="0" y="32" text-anchor="middle" font-family="Open Sans, sans-serif" font-weight="800" font-size="26" fill="#fff">?</text>
        <ellipse cx="20" cy="52" rx="24" ry="16" fill="var(--icon-grey)"/>
      </g>
      <text class="feature-label" x="105" y="355" text-anchor="middle">Questions and answers</text>

      <g class="feature feature--notes" transform="translate(300,262)">
        <rect x="-24" y="0" width="48" height="60" fill="#fff" stroke="var(--label-blue)" stroke-width="2.5"/>
        <rect x="-30" y="6" width="48" height="60" fill="#fff" stroke="var(--label-blue)" stroke-width="2.5"/>
        <g stroke="var(--icon-grey)" stroke-width="2">
          <line x1="-22" y1="22" x2="10" y2="22"/>
          <line x1="-22" y1="30" x2="10" y2="30"/>
          <line x1="-22" y1="38" x2="10" y2="38"/>
          <line x1="-22" y1="46" x2="10" y2="46"/>
          <line x1="-22" y1="54" x2="2" y2="54"/>
        </g>
      </g>
      <text class="feature-label" x="300" y="355" text-anchor="middle">Theory Notes</text>

      <g class="feature feature--tips" transform="translate(480,262)">
        <rect x="-26" y="4" width="52" height="62" rx="8" fill="#fff" stroke="var(--label-blue)" stroke-width="4"/>
        <rect x="-12" y="0" width="24" height="10" rx="3" fill="var(--label-blue)"/>
        <g fill="none" stroke="var(--label-blue)" stroke-width="3">
          <path d="M-16,24 l4,4 l7,-8"/>
          <path d="M-16,40 l4,4 l7,-8"/>
        </g>
        <g stroke="var(--icon-grey)" stroke-width="3">
          <line x1="2" y1="25" x2="18" y2="25"/>
          <line x1="2" y1="41" x2="18" y2="41"/>
          <line x1="-14" y1="55" x2="18" y2="55"/>
        </g>
      </g>
      <text class="feature-label" x="480" y="355" text-anchor="middle">Tips &amp; Tricks</text>

      <g class="feature feature--previous" transform="translate(150,400)">
        <path d="M-26,20 V44 H26 V20" fill="none" stroke="var(--label-blue)" stroke-width="5"/>
        <g stroke="var(--icon-grey)" stroke-width="5">
          <line x1="-16" y1="34" x2="16" y2="34"/>
          <line x1="-14" y1="22" x2="14" y2="10"/>
          <line x1="-8" y1="16" x2="10" y2="-2"/>
          <line x1="0" y1="14" x2="4" y2="-6"/>
        </g>
      </g>
      <text class="feature-label" x="150" y="472" text-anchor="middle">Previous Year's Reference Questions</text>

      <g class="feature feature--syllabus" transform="translate(430,400)">
        <rect x="-30" y="4" width="60" height="66" fill="var(--icon-grey)"/>
        <rect x="-34" y="0" width="60" height="66" fill="var(--brand-blue)"/>
        <g stroke="#fff" stroke-width="3">
          <line x1="-26" y1="14" x2="18" y2="14"/>
          <line x1="-26" y1="24" x2="18" y2="24"/>
          <line x1="-26" y1="34" x2="18" y2="34"/>
          <line x1="-26" y1="44" x2="18" y2="44"/>
          <line x1="-26" y1="54" x2="18" y2="54"/>
        </g>
      </g>
      <text class="feature-label" x="430" y="492" text-anchor="middle">Covers Complete Syllabus</text>

      <!-- Volume field -->
      <path class="volume-swoosh" d="M0,520 C140,500 280,560 420,552 C490,548 540,532 580,516" fill="none" stroke="var(--swoosh-grey)" stroke-width="10"/>
      <g role="img" aria-label="Dark teal field of glowing formulas and golden light points">
        <path d="M0,536 C140,516 280,576 420,568 C490,564 540,548 580,532 V816 H0 Z" fill="url(#nightField)"/>
      </g>
      <text class="volume-mark" x="290" y="720" text-anchor="middle" fill="url(#metalSilver)" stroke="#4a5056" stroke-width="1.5" filter="url(#metalDepth)">VOLUME - 1</text>
    </svg>
  </section>

</main>
</body>
</html>
```